new construction company branding

branding

Can I have a banner made so I can hang it as 1) branding my jobsite 2) advertisement

Target Market(s)

Commercial

Industry/Entity Type

Construction Trade

Font styles to use
Other font styles liked:
• Cinzel bold

Colors
EB3D1F
EC4F4E
F09395
F8D3D4
FCEDEE

Requirements
Must have
• Bright colors for advertisement
Nice to have
• 36”x48” canvas
Should not have
• To busy

```html
<!DOCTYPE html>
<html lang="en">
<head>
<meta charset="utf-8">
<title>Keystone Build Co — Business Cards</title>
<link rel="stylesheet" href="https://fonts.googleapis.com/css2?family=Cinzel:wght@400;700&family=Libre+Baskerville&family=Open+Sans:wght@400&display=swap">
<style>
  :root {
    --brand-red: #e10e0e;
    --panel-grey: #6a6a6a;
    --brand-grey: #6d6d6d;
    --paper: #ffffff;
    --backdrop: #9c9c9c;
  }
  * { margin: 0; padding: 0; box-sizing: border-box; }
  html, body { width: 1133px; height: 1200px; overflow: hidden; }
  body { background: var(--backdrop); position: relative; font-family: "Open Sans", sans-serif; }

  .card { position: absolute; left: 204px; width: 724px; height: 412px; overflow: hidden; }
  .card--front { top: 144px; background: var(--paper); }
  .card--back { top: 640px; background: var(--brand-red); }

  .card__swoosh { position: absolute; inset: 0; }

  .brand { position: absolute; text-align: center; }
  .brand__name { font-family: "Cinzel", serif; font-weight: 400; white-space: nowrap; }
  .brand__tagline { font-family: "Cinzel", serif; font-weight: 700; letter-spacing: 0.28em; white-space: nowrap; }

  .card--front .brand { left: 28px; top: 112px; width: 330px; }
  .card--front .brand__name { color: var(--brand-grey); font-size: 22px; }
  .card--front .brand__tagline { color: var(--brand-red); font-size: 16px; margin-top: 10px; }

  .card--back .brand { left: 0; top: 220px; width: 724px; }
  .card--back .brand__name { color: var(--paper); font-size: 31px; font-weight: 700; }
  .card--back .brand__tagline { color: var(--paper); font-size: 22px; margin-top: 12px; }

  .contact { position: absolute; right: 41px; top: 160px; color: var(--paper); text-align: right; }
  .contact__name { font-family: "Libre Baskerville", serif; font-size: 23px; letter-spacing: 0.02em; margin-right: 0; line-height: 1; }
  .contact__role { font-size: 15px; margin-top: 6px; letter-spacing: 0.03em; }
  .contact__list { list-style: none; margin-top: 12px; font-size: 15px; letter-spacing: 0.02em; }
  .contact__item { display: flex; justify-content: flex-end; align-items: flex-start; line-height: 20.5px; }
  .contact__item--gap { margin-top: 6px; }
  .contact__text { margin-right: 12px; }
  .contact__icon { width: 14px; height: 14px; margin-top: 3px; flex: none; fill: var(--paper); }
</style>
</head>
<body>

<section class="card card--front">
  <svg class="card__swoosh" viewBox="0 0 724 412" preserveAspectRatio="none" aria-hidden="true">
    <path d="M724 0 C520 8 300 140 221 412 L282 412 C360 170 560 22 724 0 Z" fill="var(--brand-red)"/>
    <path d="M724 0 C560 22 360 170 282 412 L724 412 Z" fill="var(--panel-grey)"/>
  </svg>

  <div class="brand">
    <p class="brand__name">KEYSTONE BUILD CO LLC</p>
    <p class="brand__tagline">GENERAL CONTRACTOR</p>
  </div>

  <div class="contact">
    <p class="contact__name">DANIEL REYES</p>
    <p class="contact__role">President</p>
    <ul class="contact__list">
      <li class="contact__item">
        <span class="contact__text">4120 Birchwood Avenue<br>Juneau, Alaska 99801</span>
        <svg class="contact__icon" viewBox="0 0 14 14"><path d="M7 0a5 5 0 0 0-5 5c0 3.5 5 9 5 9s5-5.5 5-9a5 5 0 0 0-5-5zm0 7a2 2 0 1 1 0-4 2 2 0 0 1 0 4z"/></svg>
      </li>
      <li class="contact__item contact__item--gap">
        <span class="contact__text">555-214-7730</span>
        <svg class="contact__icon" viewBox="0 0 14 14"><path d="M3 1l2.5 3-1.3 1.5c.8 1.7 2.1 3 3.8 3.8L9.5 8l3 2.5-1.5 2.5C6 12.5 1.5 8 1 3z"/></svg>
      </li>
      <li class="contact__item">
        <span class="contact__text">555-618-2094</span>
        <svg class="contact__icon" viewBox="0 0 14 14"><path d="M4 0h6a1 1 0 0 1 1 1v12a1 1 0 0 1-1 1H4a1 1 0 0 1-1-1V1a1 1 0 0 1 1-1zm.5 1.5v10h5v-10z"/></svg>
      </li>
      <li class="contact__item">
        <span class="contact__text">555-307-4461</span>
        <svg class="contact__icon" viewBox="0 0 14 14"><path d="M3 1h8v4H3zM1 6h12v5h-2V9H3v2H1zM3 10h8v3H3z"/></svg>
      </li>
      <li class="contact__item">
        <span class="contact__text">info@keystonebuildco.com</span>
        <svg class="contact__icon" viewBox="0 0 14 14"><path d="M1 3h12v8H1zM1.5 3.5 7 7.5l5.5-4" fill-rule="evenodd"/><path d="M1 3.5 7 8l6-4.5" fill="none" stroke="var(--panel-grey)" stroke-width="1"/></svg>
      </li>
      <li class="contact__item">
        <span class="contact__text">keystonebuildco.com</span>
        <svg class="contact__icon" viewBox="0 0 14 14"><circle cx="7" cy="7" r="6.5"/><path d="M2 5h10M2 9h10M7 .5c-2.5 3-2.5 10 0 13M7 .5c2.5 3 2.5 10 0 13" fill="none" stroke="var(--panel-grey)" stroke-width="1"/></svg>
      </li>
    </ul>
  </div>
</section>

<section class="card card--back">
  <div class="brand">
    <p class="brand__name">KEYSTONE BUILD CO LLC</p>
    <p class="brand__tagline">GENERAL CONTRACTOR</p>
  </div>
</section>

</body>
</html>
```